A private security company called "Tavron Security Services Ltd"

Hello everybody,

We need a web page for a company based in NZ. It is mainly an informative website so it would be wonderful if the designer puts their absolute best into making it a website that I would really appreciate. The website needs to show professionalism and also needs to make our web surfers find the information they need in a click. the company's colour is black and silver, and if those two colours could be integrated into the website it would be absolutely lovely. Please do contact me for any information.

Sincerely,
Dorian Vaskel

Industry/Entity Type

Security

```html
<!DOCTYPE html>
<html lang="en">
<head>
<meta charset="utf-8">
<title>Tavron Security Services Ltd</title>
<link href="https://fonts.googleapis.com/css2?family=Open+Sans:wght@300;400;600;700&family=Montserrat:wght@400;500&display=swap" rel="stylesheet">
<style>
:root{
  --ink:#222222;
  --panel:#2b2b2b;
  --footer:#262626;
  --silver:#c4c4c4;
  --silver-light:#dcdcdc;
  --text:#6f6f6f;
  --muted:#a9a9a9;
  --white:#ffffff;
  --field:#1c1c1c;
}
*{box-sizing:border-box;margin:0;padding:0}
html,body{width:897px;height:1200px;overflow:hidden;background:var(--white)}
body{position:relative;font-family:"Open Sans",Arial,sans-serif;color:var(--text)}
.abs{position:absolute}

/* header */
.site-header{left:0;top:0;width:897px;height:104px;background:var(--ink)}
.brand{left:82px;top:30px;color:var(--white);text-align:center;width:120px}
.brand-mark{width:14px;height:14px;background:var(--silver);margin:0 auto 6px}
.brand-name{font-weight:700;font-size:20px;letter-spacing:2px;line-height:1}
.brand-sub{font-weight:700;font-size:7.5px;letter-spacing:.4px;margin-top:3px}
.hotline{left:604px;top:30px;color:var(--white);font-family:"Montserrat",Arial,sans-serif}
.hotline svg{position:absolute;left:0;top:0}
.hotline-number{position:absolute;left:44px;top:-1px;font-size:22px;font-weight:500;white-space:nowrap}
.hotline-note{position:absolute;left:44px;top:28px;font-size:12.5px;white-space:nowrap}

/* nav */
.main-nav{left:0;top:104px;width:897px;height:40px;background:linear-gradient(#fafafa,#e9e9e9)}
.nav-item{position:absolute;top:0;height:40px;line-height:40px;font-size:10.5px;color:#333;text-transform:uppercase}
.nav-item.active{background:var(--silver);padding:0 15px;left:83px}
.search{position:absolute;left:658px;top:7px;width:157px;height:26px;background:#e2e2e2;border:1px solid #d0d0d0}
.search span{position:absolute;left:8px;top:5px;font-size:9.5px;font-style:italic;color:#999}
.search svg{position:absolute;right:6px;top:5px}

/* hero */
.hero{left:0;top:144px;width:897px;height:341px}
.hero-photo{position:absolute;inset:0;background:linear-gradient(90deg,#18302c 0%,#1d3a48 40%,#4a5b6a 58%,#d7dad9 72%,#eeeeee 100%)}
.hero-copy{position:absolute;left:82px;top:105px;color:var(--white);width:300px}
.hero-title{font-size:27px;font-weight:600;line-height:34px}
.hero-sub{font-size:27px;font-weight:300;line-height:34px}
.hero-text{font-size:9.5px;line-height:15px;color:#c9cfd0;margin-top:8px}
.btn-arrow{position:absolute;left:82px;top:221px}

/* services */
.services{left:82px;top:507px;width:196px;height:427px;background:var(--panel)}
.services h2{position:absolute;left:13px;top:8px;font-size:18px;font-weight:400;color:var(--white)}
.service-card{position:absolute;left:15px;width:166px}
.service-label{height:24px;line-height:24px;padding-left:6px;background:var(--silver-light);color:#222;font-size:11.5px;font-weight:600;text-transform:uppercase}
.service-photo{height:90px}
.service-text{font-size:9.5px;line-height:13.5px;color:#ddd;margin-top:11px}
.service-rule{position:absolute;left:15px;width:166px;height:1px;background:#444}
.all-services{position:absolute;left:15px;top:391px;width:166px;height:28px;line-height:28px;text-align:center;background:var(--silver);color:#222;font-size:11px;text-transform:uppercase}

/* content */
.block-title{background:var(--panel);color:var(--white);font-size:15px;height:32px;line-height:32px;padding-left:9px}
.feature{top:507px;width:249px}
.feature-photo{height:107px;margin-top:8px}
.feature h3{font-size:10.5px;font-weight:600;color:#222;margin-top:17px;text-transform:uppercase}
.feature p{font-size:9.8px;line-height:15px;margin-top:7px}
.read-more{display:inline-block;background:var(--silver);color:#222;font-size:12px;height:28px;line-height:28px;padding:0 8px;margin-top:11px}
.about{left:298px;top:790px;width:517px}
.about p{font-size:9.8px;line-height:15px;margin-top:13px}
.about .read-more{margin-top:14px}

/* footer */
.site-footer{left:0;top:958px;width:897px;height:204px;background:var(--footer)}
.footer-col{position:absolute;top:0;height:204px}
.footer-col h4{position:absolute;top:19px;font-size:12px;font-weight:600;color:var(--white);text-transform:uppercase;white-space:nowrap}
.footer-list{position:absolute;top:44px;list-style:none;font-size:9.8px;line-height:16.4px;color:var(--muted);white-space:nowrap}
.divider{position:absolute;top:0;width:1px;height:204px;background:#1a1a1a}
.quote{position:absolute;top:44px;width:200px;font-size:9.8px;line-height:16.4px;color:var(--muted)}
.quote-author{position:absolute;top:94px;font-size:9.8px;color:var(--white);text-decoration:underline}
.field{position:absolute;left:638px;width:168px;background:var(--field);font-size:9px;font-style:italic;color:#777;padding:7px 9px}
.send{position:absolute;left:735px;top:160px;width:71px;height:27px;line-height:27px;text-align:center;background:linear-gradient(#fff,#ddd);color:#333;font-size:11px;text-transform:uppercase}

.copyright{left:0;top:1162px;width:897px;height:38px;line-height:38px;text-align:center;font-size:9.8px;color:#333}
</style>
</head>
<body>

<header class="site-header abs">
  <div class="brand abs">
    <div class="brand-mark"></div>
    <div class="brand-name">TAVRON</div>
    <div class="brand-sub">SECURITY SERVICES LTD.</div>
  </div>
  <div class="hotline abs">
    <svg width="38" height="38" viewBox="0 0 38 38" aria-hidden="true">
      <path d="M10 6c-5 4-5 16 3 24 4 4 7 5 9 4l2-4-5-4-3 2c-3-3-5-7-5-10l3-2-2-6z" fill="none" stroke="#fff" stroke-width="2.2"/>
      <path d="M22 6a10 10 0 0 1 9 9M21 11a5 5 0 0 1 5 5" fill="none" stroke="#fff" stroke-width="2"/>
    </svg>
    <div class="hotline-number">0800-555-0192-4</div>
    <div class="hotline-note">Call Us Now For Free Quote</div>
  </div>
</header>

<nav class="main-nav abs">
  <span class="nav-item active">Home</span>
  <span class="nav-item" style="left:159px">About Us</span>
  <span class="nav-item" style="left:239px">Security System</span>
  <span class="nav-item" style="left:356px">Specialized Security</span>
  <span class="nav-item" style="left:496px">Carrers</span>
  <span class="nav-item" style="left:570px">Contact Us</span>
  <div class="search">
    <span>Search here..</span>
    <svg width="16" height="16" viewBox="0 0 16 16" aria-hidden="true"><circle cx="6.5" cy="6.5" r="5" fill="none" stroke="#999" stroke-width="1.6"/><path d="M10 10l4.5 4.5" stroke="#999" stroke-width="1.8"/></svg>
  </div>
</nav>

<section class="hero abs">
  <div class="hero-photo" role="img" aria-label="White CCTV camera mounted on a wall beside a blurred dark glass facade"></div>
  <div class="hero-copy">
    <div class="hero-title">Newzealand’s Best</div>
    <div class="hero-sub">Security Company</div>
    <p class="hero-text">Lorem ipsum dolor sit amet, consectetur adipisicing elit, sed do eiusmod tempor incididunt dolore magna aliqua..</p>
  </div>
  <svg class="btn-arrow" width="100" height="28" viewBox="0 0 100 28">
    <path d="M0 0h86l13 14-13 14H0z" fill="#d4d4d4"/>
    <text x="13" y="18.5" font-family="Open Sans, sans-serif" font-size="12" fill="#222">Learn More</text>
  </svg>
</section>

<aside class="services abs">
  <h2>Our Services</h2>
  <div class="service-card" style="top:40px">
    <div class="service-label">Property Guards</div>
    <div class="service-photo" role="img" aria-label="Guard in a dark security jacket seen from behind" style="background:linear-gradient(135deg,#8a8f93,#2c3038 55%,#1f232a)"></div>
    <p class="service-text">Lorem ipsum dolor sit amet consect-etur adipisicing elit.</p>
  </div>
  <div class="service-rule" style="top:201px"></div>
  <div class="service-card" style="top:219px">
    <div class="service-label">Security Consultancy</div>
    <div class="service-photo" role="img" aria-label="Operators in front of a wall of surveillance monitors" style="background:linear-gradient(135deg,#5a6a80,#2a3040 60%,#6e5a4c)"></div>
    <p class="service-text">Lorem ipsum dolor sit amet consect-etur adipisicing elit.</p>
  </div>
  <div class="service-rule" style="top:381px"></div>
  <div class="all-services">View All Services</div>
</aside>

<article class="feature abs" style="left:298px">
  <div class="block-title">Welcome to Tavron</div>
  <div class="feature-photo" role="img" aria-label="Team reviewing documents in a bright office" style="background:linear-gradient(90deg,#b7b3ad,#7d7670 50%,#c8c2b8)"></div>
  <h3>Lorem ipsum dolor sit amet</h3>
  <p>Lorem ipsum dolor sit amet, consectetur adipisicing elit, sed do eiusmod tempor incididunt ut labore et dolore magna aliqua.</p>
  <span class="read-more">Read More</span>
</article>

<article class="feature abs" style="left:566px">
  <div class="block-title">Security System</div>
  <div class="feature-photo" role="img" aria-label="Operator watching a bank of CCTV monitors" style="background:linear-gradient(90deg,#3c5a8a,#5a7fb8 50%,#4d8fc8 75%,#2c4060)"></div>
  <h3>Lorem ipsum dolor sit amet</h3>
  <p>Lorem ipsum dolor sit amet, consectetur adipisicing elit, sed do eiusmod tempor incididunt ut labore et dolore magna aliqua.</p>
  <span class="read-more">Read More</span>
</article>

<section class="about abs">
  <div class="block-title">About Tavron</div>
  <p>Lorem ipsum dolor sit amet, consectetur adipisicing elit, sed do eiusmod tempor incididunt ut labore et dolore magna aliqua. Ut enim ad minim veniam, quis nostrud exercitation ullamco laboris nisi ut aliquip ex ea commodo consequat in voluptate velit esse cillum dolore eu fugiat nulla pariatur. Excepteur sint occaecat cupidatat non proident, sunt in culpa qui officia deserunt mollit anim id est laborum..</p>
  <span class="read-more">Read More</span>
</section>

<footer class="site-footer abs">
  <div class="footer-col" style="left:82px">
    <h4>Site Map</h4>
    <ul class="footer-list"><li>Home</li><li>About Us</li><li>Security System</li><li>Specialized Security</li><li>Carrers</li><li>Contact Us</li></ul>
  </div>
  <div class="divider" style="left:203px"></div>
  <div class="footer-col" style="left:235px">
    <h4>Links</h4>
    <ul class="footer-list"><li>Lorem ipsum</li><li>Dolor sit Amet</li><li>consectetur aDipsicing</li><li>Elit, Sed Do Euismod</li><li>Tempor incidunt</li><li>Magna Aliqua</li></ul>
  </div>
  <div class="divider" style="left:367px"></div>
  <div class="footer-col" style="left:398px">
    <h4>Testimonials</h4>
    <p class="quote">“Lorem ipsum dolor sit amet, consectetur adipisicing elit, sed do eiusmod tempor incididunt magna aliqua”</p>
    <span class="quote-author">Corwin Hale</span>
  </div>
  <div class="divider" style="left:610px"></div>
  <h4 class="abs" style="left:638px;top:19px;font-size:12px;font-weight:600;color:#fff">QUICK CONTACT</h4>
  <div class="field" style="top:48px;height:24px">Name</div>
  <div class="field" style="top:76px;height:24px">Email</div>
  <div class="field" style="top:106px;height:46px">Message</div>
  <div class="send">Send</div>
</footer>

<div class="copyright abs">Copyrights © 2014 Tavron .com - All Rights Reserved</div>

</body>
</html>
```